Specialised investor in e-mobility and energy wants business card design

We need a business card design that fits our existing corporate design. <The look and feel must be 'sharp'/'clean', dynamic, communicate momentum, professionalism etc (as one would imagine from a firm in the financial sector). We like the idea of a reverse-side of the card that includes the logo, and the name and contact details on the other. We expect the deliverable to be whatever format might be required to be able to get cards printed directly by a service such as kelmo press. Our website is www.zub.capital

```html
<!DOCTYPE html>
<html lang="en">
<head>
<meta charset="utf-8">
<title>Zub Capital – Business Card</title>
<link href="https://fonts.googleapis.com/css2?family=Montserrat:wght@300;400;700&display=swap" rel="stylesheet">
<style>
  :root {
    --green-dark: #2f5128;
    --green-light: #7bb33f;
    --ink: #2a2a2a;
    --paper: #ffffff;
    --backdrop: #e9ebe7;
  }
  * { margin: 0; padding: 0; box-sizing: border-box; }
  html, body { width: 1200px; height: 960px; overflow: hidden; }
  body {
    background: var(--backdrop);
    font-family: "Montserrat", Arial, sans-serif;
    display: flex; flex-direction: column; align-items: center; justify-content: center;
    gap: 44px;
  }
  .card {
    position: relative;
    width: 720px; height: 411px;
    border-radius: 34px;
    overflow: hidden;
    box-shadow: 0 6px 18px rgba(0,0,0,0.12);
  }
  .card-back { background: var(--green-dark); display: flex; align-items: center; justify-content: center; }
  .card-back .wordmark { color: var(--paper); font-size: 84px; }
  .wordmark {
    font-family: "Montserrat", Arial, sans-serif;
    font-weight: 300; letter-spacing: 1px; line-height: 1;
    display: flex; align-items: center; gap: 20px;
  }
  .wordmark .dot { width: 18px; height: 18px; border-radius: 50%; background: currentColor; }

  .card-front { background: var(--paper); }
  .card-front .wordmark { position: absolute; left: 64px; top: 70px; color: var(--green-dark); font-size: 70px; }
  .divider-long { position: absolute; left: 330px; right: 40px; top: 200px; height: 2px; background: var(--green-light); }
  .company-address {
    position: absolute; right: 48px; top: 138px;
    text-align: right; font-weight: 400; font-size: 17px; line-height: 1.35; color: var(--ink);
  }
  .person { position: absolute; left: 64px; top: 224px; }
  .person-name { font-weight: 700; font-size: 25px; letter-spacing: 1px; color: var(--green-light); text-transform: uppercase; }
  .person-role { font-weight: 400; font-size: 17px; color: var(--ink); margin-top: 4px; }
  .divider-short { width: 220px; height: 2px; background: var(--green-light); margin: 14px 0 12px; }
  .contact-list { list-style: none; }
  .contact-list li { display: flex; align-items: center; gap: 12px; font-size: 17px; color: var(--ink); line-height: 1.55; }
  .contact-list svg { width: 16px; height: 16px; flex: none; }
</style>
</head>
<body>
  <section class="card card-back">
    <div class="wordmark"><span class="dot"></span>Zub Capital</div>
  </section>

  <section class="card card-front">
    <div class="wordmark"><span class="dot"></span>Zub Capital</div>
    <div class="company-address">Zub Capital S.A.<br>Geneva, Switzerland</div>
    <div class="divider-long"></div>
    <div class="person">
      <div class="person-name">Marcus Hallberg</div>
      <div class="person-role">Managing Director</div>
      <div class="divider-short"></div>
      <ul class="contact-list">
        <li>
          <svg viewBox="0 0 16 16" aria-hidden="true"><path fill="var(--green-light)" d="M3 2l3 0 1 3-2 1.5c.8 1.7 2 2.9 3.5 3.5L10 8l3 1v3c0 .6-.5 1-1 1C6.5 13 3 9.5 2 4c0-1 .4-2 1-2z"/></svg>
          +41 79555 0142
        </li>
        <li>
          <svg viewBox="0 0 16 16" aria-hidden="true"><rect x="1" y="3" width="14" height="10" rx="1" fill="var(--green-light)"/><path d="M1.5 4 8 9l6.5-5" stroke="#fff" stroke-width="1.3" fill="none"/></svg>
          marcus@zub.capital
        </li>
        <li>
          <svg viewBox="0 0 16 16" aria-hidden="true"><circle cx="8" cy="8" r="7" fill="var(--green-light)"/><path d="M1 8h14M8 1c-3 3.5-3 10.5 0 14M8 1c3 3.5 3 10.5 0 14" stroke="#fff" stroke-width="1" fill="none"/></svg>
          www.zub.capital
        </li>
      </ul>
    </div>
  </section>
</body>
</html>
```